Brell Stone Company Business Cards

Front and Back Business Card - logo and text setup - cool design. I need workable photoshop or illustrator files so I can setup each employee card with design that is created
Updates

Hi everyone, thank you for the great entries. Please no more white and blue cards - there are so many already - black and silver only now please. thanks!

Target Market(s)

Construction Industry - Facility Managers

Industry/Entity Type

Construction

Contact Information for Business Card

I really like contemporary simplistic looks - clean neat....not opposed to seeing some black backrounds

Requirements
Must have
• Logo/website address with design on front only - www.brellstone-example.com (logo attached)
• Back:
• Name/Title/Company Address/Phone/email address
Nice to have
• Cool design
Should not have
• Nothing gimmicky like Fire or Water - since we are a Fire Protection company - it has all been done

```html
<!DOCTYPE html>
<html lang="en">
<head>
<meta charset="utf-8">
<title>Brell Stone Company Business Cards</title>
<link rel="stylesheet" href="https://fonts.googleapis.com/css2?family=Open+Sans:wght@400;600;700;800&display=swap">
<style>
  :root {
    --page-bg: #c9ccd0;
    --card-black: #0b0b0b;
    --card-charcoal: #1c1c1c;
    --brand-red: #ff2222;
    --brand-blue: #0624a0;
    --text-white: #ffffff;
    --divider: #4a4a4a;
    --mark-grey: #6e6e6e;
  }
  * { margin: 0; padding: 0; box-sizing: border-box; }
  html, body { width: 1200px; height: 1193px; overflow: hidden; }
  body {
    background: var(--page-bg);
    font-family: "Open Sans", Arial, sans-serif;
    position: relative;
  }
  .card {
    position: absolute;
    left: 150px;
    width: 900px;
    height: 514px;
    border-radius: 40px;
    overflow: hidden;
    background: radial-gradient(ellipse at 45% 30%, var(--card-charcoal) 0%, var(--card-black) 70%);
  }
  .card-front { top: 50px; }
  .card-back { top: 629px; }

  .swoosh { position: absolute; left: 0; top: 0; width: 900px; height: 514px; }

  .front-name {
    position: absolute;
    left: 92px; top: 175px;
    font-size: 66px;
    font-weight: 800;
    color: var(--brand-blue);
    letter-spacing: -1px;
  }
  .divider {
    position: absolute;
    left: 478px; top: 78px;
    width: 2px; height: 275px;
    background: var(--divider);
  }
  .contact {
    position: absolute;
    left: 512px; top: 72px;
    color: var(--text-white);
  }
  .person-name { font-size: 30px; font-weight: 700; line-height: 1.15; }
  .person-title { font-size: 26px; font-weight: 400; line-height: 1.3; margin-bottom: 16px; }
  .contact-line {
    display: flex; align-items: center; gap: 12px;
    font-size: 21px; line-height: 1.85;
  }
  .contact-line svg { width: 22px; height: 22px; flex: none; }
  .address { font-size: 23px; line-height: 1.45; margin-top: 14px; }

  .back-name {
    position: absolute;
    left: 0; right: 0; top: 160px;
    text-align: center;
    font-size: 104px;
    font-weight: 800;
    color: var(--mark-grey);
    letter-spacing: -2px;
  }
  .back-web {
    position: absolute;
    left: 0; right: 0; top: 330px;
    text-align: center;
    font-size: 30px;
    letter-spacing: 6px;
    color: var(--text-white);
  }
</style>
</head>
<body>
  <section class="card card-front">
    <svg class="swoosh" viewBox="0 0 900 514" aria-hidden="true">
      <path fill="var(--brand-red)" d="M0 345 Q350 420 700 478 Q330 440 0 396 Z"/>
      <path fill="var(--brand-blue)" d="M0 404 Q420 468 812 450 L742 514 L0 514 Z"/>
      <path fill="var(--brand-red)" d="M758 514 L900 436 L900 514 Z"/>
    </svg>
    <div class="front-name">Brell Stone</div>
    <div class="divider"></div>
    <div class="contact">
      <div class="person-name">Dana Mercer</div>
      <div class="person-title">President</div>
      <div class="contact-line">
        <svg viewBox="0 0 24 24" aria-hidden="true"><path fill="var(--brand-red)" d="M6.6 10.8a15 15 0 0 0 6.6 6.6l2.2-2.2a1 1 0 0 1 1-.25 11.4 11.4 0 0 0 3.6.57 1 1 0 0 1 1 1V20a1 1 0 0 1-1 1A17 17 0 0 1 3 4a1 1 0 0 1 1-1h3.5a1 1 0 0 1 1 1c0 1.25.2 2.45.57 3.57a1 1 0 0 1-.25 1z"/></svg>
        <span>(555) 014-2290</span>
      </div>
      <div class="contact-line">
        <svg viewBox="0 0 24 24" aria-hidden="true"><rect x="2" y="5" width="20" height="14" fill="var(--brand-red)"/><path d="M2 5l10 8 10-8" fill="none" stroke="var(--card-black)" stroke-width="1.6"/></svg>
        <span>info@brellstone-example.com</span>
      </div>
      <div class="contact-line">
        <svg viewBox="0 0 24 24" aria-hidden="true"><g fill="none" stroke="var(--brand-red)" stroke-width="1.6"><circle cx="12" cy="12" r="10"/><ellipse cx="12" cy="12" rx="4.5" ry="10"/><path d="M2 12h20M4 7h16M4 17h16"/></g></svg>
        <span>www.brellstone-example.com</span>
      </div>
      <div class="address">48 Harbor Park Road<br>Millbrook, NY 10599</div>
    </div>
  </section>

  <section class="card card-back">
    <div class="back-name">Brell Stone</div>
    <div class="back-web">www.brellstone-example.com</div>
  </section>
</body>
</html>
```